KRL Stationery Design Project

Dear Designers,
We need a new stationery design for company to match our new logo.
Designers should provide a design for the following:
1. Business Card: 3.5x2 Inches.
2. Letterhead: A4 size.
3. Envelops: 25x35.5 Cm.
You can keep the Arabic name at the bottom of the logo Or you can use the separate attached Arabic Name.
Please refer to the attached logo guide for design information.
Sample Business Card information:
Name: Tarek Sowan
Position: Operation Manager
Tel: +966 920007164 Ex. 500
Fax: +966 (3)8842617
Mob: +966 (5)00263817
email: tarek@krl-example.com.sa
URL: www.krl-example.com.sa
Address:
Nakheel Heights, Suite 718
Zayed bin Omar Str.
Khobar, 31847
Saudi Arabia
Updates
Dear All,
Please note, we had uploaded our logo along with Arabic writing in Adobe illustrator format (.ai).
Regards,
Karim
Dear All,
A sample data for the business card had been added as per your request.
Regards,
Karim

```html
<!DOCTYPE html>
<html lang="en">
<head>
<meta charset="utf-8">
<title>KRL Business Card</title>
<link href="https://fonts.googleapis.com/css2?family=Open+Sans:wght@400;700&display=swap" rel="stylesheet">
<style>
  :root {
    --backdrop: #2b2b2d;
    --card: #ffffff;
    --navy: #0f3155;
    --grey-band: #a7a7a7;
    --ink: #3a3a3a;
  }
  html, body {
    margin: 0;
    width: 960px;
    height: 1200px;
    overflow: hidden;
    background: var(--backdrop);
    font-family: "Open Sans", Arial, sans-serif;
  }
  .card {
    position: absolute;
    left: 60px;
    width: 840px;
    height: 479px;
    background: var(--card);
    border-radius: 30px;
    overflow: hidden;
  }
  .card--front { top: 88px; }
  .card--back { top: 643px; }

  .brand {
    position: absolute;
    display: flex;
    align-items: center;
    gap: 22px;
    color: var(--navy);
    font-weight: 700;
    line-height: 1;
  }
  .brand__mark {
    background: var(--navy);
  }
  .card--front .brand { left: 100px; top: 90px; font-size: 110px; }
  .card--front .brand__mark { width: 60px; height: 60px; }
  .card--back .brand { left: 50%; top: 50%; transform: translate(-50%, -50%); font-size: 130px; }
  .card--back .brand__mark { width: 72px; height: 72px; }

  .contact {
    position: absolute;
    left: 58px;
    top: 278px;
    color: var(--ink);
    font-size: 19px;
    line-height: 28px;
  }
  .contact__name { font-size: 24px; margin-bottom: 10px; }
  .contact__role { font-size: 19px; }
  .contact__line { display: flex; align-items: center; gap: 8px; }
  .contact__line svg { width: 16px; height: 16px; fill: var(--ink); }
  .contact__gap { width: 10px; }
  .contact__address { margin-top: 9px; }

  .band {
    position: absolute;
    left: 0;
    bottom: 0;
    width: 100%;
    height: 19px;
    background: var(--grey-band);
  }
  .band__accent {
    position: absolute;
    left: 255px;
    width: 330px;
    height: 100%;
    background: var(--navy);
  }
</style>
</head>
<body>
  <section class="card card--front">
    <div class="brand"><span class="brand__mark"></span><span>KRL</span></div>

    <div class="contact">
      <div class="contact__name">Your Name - <span class="contact__role">Designation</span></div>
      <div class="contact__line">
        <svg viewBox="0 0 16 16" aria-hidden="true"><path d="M1 6c0-3 14-3 14 0v1h-4V5.5H5V7H1zM3 8l2-2h6l2 2v6H3z"/></svg>
        <span>123-123-1234</span>
        <span class="contact__gap"></span>
        <svg viewBox="0 0 16 16" aria-hidden="true"><path d="M4 1h8v4H4zM1 6h14v7h-3v2H4v-2H1zM5 10v4h6v-4z"/></svg>
        <span>123-123-1234</span>
      </div>
      <div class="contact__line">
        <svg viewBox="0 0 16 16" aria-hidden="true"><path d="M8 2a6 6 0 1 0 3 11.2l-.7-1.3A4.5 4.5 0 1 1 12.5 8v1a1 1 0 0 1-2 0V5h-1.3v.5A3 3 0 1 0 10.8 10.5 2.4 2.4 0 0 0 14 9V8a6 6 0 0 0-6-6zm0 4.4A1.6 1.6 0 1 1 8 9.6 1.6 1.6 0 0 1 8 6.4z"/></svg>
        <span>info@krl-example.com.sa</span>
      </div>
      <div class="contact__line">
        <svg viewBox="0 0 16 16" aria-hidden="true"><circle cx="8" cy="8" r="6.5"/></svg>
        <span>www.krl-example.com.sa</span>
      </div>
      <div class="contact__address">1234, Suite# 123, Street Name, State NAME, Country Code</div>
    </div>

    <div class="band"><div class="band__accent"></div></div>
  </section>

  <section class="card card--back">
    <div class="brand"><span class="brand__mark"></span><span>KRL</span></div>
  </section>
</body>
</html>
```